New Business Card Design Project

Need a design that will create an impact / strong impression towards our clients for our business. We are in the lighting business and we do lighting retrofits for large commercial to industrial clientele.

Target Market(s)

Lighting Industry

Industry/Entity Type

Business

Font styles to use
Other font styles liked:
• we would like to use the font on our logo, not sure what it is though..

Requirements
Must have
• Our logo.
Nice to have
• We are open to suggestions that have to do with lighting.

```html
<!DOCTYPE html>
<html lang="en">
<head>
<meta charset="utf-8">
<title>Lumenway Retrofit Co. — Business Card</title>
<link rel="stylesheet" href="https://fonts.googleapis.com/css2?family=Roboto+Condensed:wght@400;700&display=swap">
<style>
  :root {
    --stage: #e7e4df;
    --green-deep: #0f4a1c;
    --green-mid: #1a8a45;
    --green-light: #6ccb5f;
    --paper: #f6f6f4;
    --ink-light: #ffffff;
    --ink-grey: #6d6d6d;
    --brand-green: #136d2c;
  }
  * { box-sizing: border-box; margin: 0; padding: 0; }
  html, body { width: 1200px; height: 911px; overflow: hidden; }
  body {
    background: var(--stage);
    font-family: "Roboto Condensed", Arial, sans-serif;
    position: relative;
  }
  .card {
    position: absolute;
    width: 525px;
    height: 300px;
    border-radius: 18px;
    overflow: hidden;
    box-shadow: 0 10px 26px rgba(0,0,0,.22);
  }
  /* Front: dark green card */
  .card--front {
    left: 50px; top: 305px;
    background: linear-gradient(135deg, var(--green-deep) 0%, #1d5c2a 55%, var(--green-deep) 100%);
    color: var(--ink-light);
  }
  .accent-panel {
    position: absolute;
    right: 0; top: 0;
    width: 200px; height: 100%;
    background: linear-gradient(180deg, #ffffff 0%, var(--green-mid) 35%, var(--green-light) 60%, var(--green-mid) 85%, var(--green-light) 100%);
  }
  .front-content {
    position: absolute;
    left: 34px; top: 30px;
  }
  .brand-name {
    font-weight: 700;
    font-size: 30px;
    letter-spacing: 1px;
    line-height: 1;
  }
  .brand-rule {
    width: 230px; height: 1px;
    background: rgba(255,255,255,.7);
    margin: 8px 0 6px;
  }
  .brand-tag {
    font-size: 10px;
    letter-spacing: 1.5px;
    text-transform: uppercase;
  }
  .person-name {
    margin-top: 22px;
    font-weight: 700;
    font-size: 21px;
    text-transform: uppercase;
    letter-spacing: .5px;
  }
  .person-title {
    font-size: 14px;
    text-transform: uppercase;
    margin-top: 2px;
  }
  .address {
    margin-top: 14px;
    font-size: 13px;
    line-height: 1.35;
  }
  .contact-list {
    list-style: none;
    margin-top: 10px;
    font-size: 13px;
    line-height: 1.38;
  }
  .contact-list li { display: flex; align-items: center; gap: 7px; }
  .contact-list svg { width: 11px; height: 11px; flex: none; }

  /* Back: white card */
  .card--back {
    left: 625px; top: 305px;
    background: var(--paper);
  }
  .back-brand {
    position: absolute;
    left: 0; right: 0; top: 95px;
    text-align: center;
    color: var(--brand-green);
  }
  .back-brand .brand-name { font-size: 40px; }
  .back-brand .brand-rule {
    background: var(--brand-green);
    width: 290px;
    margin: 10px auto 7px;
  }
  .back-brand .brand-tag { font-size: 11px; font-weight: 700; }
  .website {
    position: absolute;
    left: 0; right: 0; bottom: 40px;
    text-align: center;
    font-size: 13px;
    letter-spacing: 3px;
    color: var(--ink-grey);
  }
</style>
</head>
<body>

<section class="card card--front" aria-label="Business card front">
  <div class="accent-panel" role="img" aria-label="Decorative band of layered green and white stripes"></div>
  <div class="front-content">
    <div class="brand-name">LUMENWAY</div>
    <div class="brand-rule"></div>
    <div class="brand-tag">Lumenway Retrofit Co.</div>

    <div class="person-name">Dana Whitfield</div>
    <div class="person-title">CEO/Founder</div>

    <div class="address">1420 Harbor View Road<br>Fairbanks, Alaska 99701</div>

    <ul class="contact-list">
      <li>
        <svg viewBox="0 0 12 12" aria-hidden="true"><path fill="currentColor" d="M2.5 1l2 2-1 1.3c.7 1.5 1.8 2.6 3.2 3.2L8 6.5l2 2L8.8 10.5C4.8 10 2 7.2 1.5 3.2z"/></svg>
        907 555 0142
      </li>
      <li>
        <svg viewBox="0 0 12 12" aria-hidden="true"><rect x="3" y="1" width="6" height="10" rx="1" fill="none" stroke="currentColor" stroke-width="1.2"/></svg>
        907 555 0187
      </li>
      <li>
        <svg viewBox="0 0 12 12" aria-hidden="true"><rect x="1.5" y="3" width="9" height="7" fill="currentColor"/><rect x="3.5" y="1" width="5" height="3" fill="currentColor"/></svg>
        907 555 0163
      </li>
      <li>
        <svg viewBox="0 0 12 12" aria-hidden="true"><rect x="1" y="2.5" width="10" height="7" fill="currentColor"/><path d="M1 2.5l5 4 5-4" fill="none" stroke="#0f4a1c" stroke-width="1"/></svg>
        dana@lumenway.com
      </li>
      <li>
        <svg viewBox="0 0 12 12" aria-hidden="true"><circle cx="6" cy="6" r="5" fill="currentColor"/><path d="M1 6h10M6 1c2 2.5 2 7.5 0 10M6 1c-2 2.5-2 7.5 0 10" fill="none" stroke="#0f4a1c" stroke-width=".8"/></svg>
        www.lumenway.com
      </li>
    </ul>
  </div>
</section>

<section class="card card--back" aria-label="Business card back">
  <div class="back-brand">
    <div class="brand-name">LUMENWAY</div>
    <div class="brand-rule"></div>
    <div class="brand-tag">Lumenway Retrofit Co.</div>
  </div>
  <div class="website">www.lumenwayretrofit.com</div>
</section>

</body>
</html>
```